Flyer for Yoga and IronPulse.

Just initial idea and open to creativity: I am thinking right half of flyer to be IronPulse info and left half to be Yoga info.
Feel free to add text as needed but would like following:
Basic text: ZenLoftVo $69/mo unlimited sessions.
ZenLoftVO.com
IronPulse: $99 intro session. Largest IronPulse in Texas.
IronPulseVO.com

Located North Riverside Houston (NRVO)
Address: 4817 Marlow Pkwy Houston, tx

Please submit any and all designs. Looking to get some great ideas!

Target Market(s)

Young professionals free spirited and fun atmosphere.

Colors
3176b5
85acd3
32a6d7
32b7a4
f59195
cde9f5
f04a50

Requirements
Must have
• Professional yet fun. Text should include:
ZenLoftVo and IronPulse Vo taking each a half of the page seperatly get still be identifiable as one. Want to show there is two options for either yoga or IronPulse or do both!
IronPulse Intro is $99 adm yoga intro is $69.
Nice to have
• Also visit www.ironpulsevo.com for more ideas and info.

```html
<!DOCTYPE html>
<html lang="en">
<head>
<meta charset="utf-8">
<title>IronPulse Vo &amp; ZenLoftVo Flyer</title>
<link rel="stylesheet" href="https://fonts.googleapis.com/css2?family=Bebas+Neue&family=Open+Sans:wght@400&display=swap">
<style>
  :root {
    --red: #c1272d;
    --teal: #22bccb;
    --ink: #231f20;
    --amber: #f0a040;
    --white: #ffffff;
    --photo-gym-a: #6f6a62;
    --photo-gym-b: #b9b2a6;
    --photo-yoga-a: #f3e6d2;
    --photo-yoga-b: #e9b57a;
  }
  * { margin: 0; padding: 0; box-sizing: border-box; }
  html, body { width: 934px; height: 1200px; overflow: hidden; background: var(--white); }
  .canvas {
    position: relative; width: 750px; height: 963px;
    transform: scale(1.24533); transform-origin: 0 0;
  }
  .sheet {
    position: absolute; left: 99px; top: 73px; width: 554px; height: 808px;
    border: 1px solid var(--ink);
  }
  .abs { position: absolute; }
  .display { font-family: "Bebas Neue", "Arial Narrow", sans-serif; line-height: 1; white-space: nowrap; }
  .body-copy { font-family: "Open Sans", Arial, sans-serif; font-size: 11.3px; line-height: 14.4px; color: var(--ink); }

  .gym-photo {
    left: 320px; top: 82px; width: 323px; height: 365px;
    background: linear-gradient(135deg, var(--photo-gym-b), var(--photo-gym-a) 55%, #4b4640);
    clip-path: polygon(0 0, 100% 0, 100% 80.3%, 0 100%);
  }
  .red-band { left: 108px; top: 82px; width: 422px; height: 100px; }
  .band-url { left: 127px; top: 103px; font-size: 27px; color: var(--white); }

  .gym-name { left: 140px; top: 200px; width: 160px; text-align: center; font-size: 40px; color: var(--red); }
  .gym-copy { left: 140px; top: 268px; width: 170px; }

  .tag { background: var(--white); display: flex; align-items: center; }
  .gym-offer { left: 385px; top: 280px; width: 258px; height: 43px; padding-left: 16px; font-size: 33px; color: var(--red); }
  .gym-claim { left: 325px; top: 330px; width: 318px; height: 40px; padding-left: 19px; font-size: 31px; color: var(--ink); }

  .yoga-mark { left: 530px; top: 422px; width: 22px; height: 22px; border-radius: 50%; background: var(--teal); }
  .yoga-name { left: 470px; top: 455px; width: 145px; text-align: center; font-size: 40px; color: var(--red); }
  .yoga-copy { left: 477px; top: 555px; width: 152px; }

  .yoga-photo {
    left: 108px; top: 432px; width: 324px; height: 390px;
    background: linear-gradient(160deg, var(--photo-yoga-a) 20%, #f6d9b3 55%, var(--photo-yoga-b));
    clip-path: polygon(0 9.7%, 100% 0, 100% 100%, 0 100%);
  }
  .teal-band { left: 230px; top: 722px; width: 413px; height: 100px; }
  .band-url-teal { left: 493px; top: 778px; font-size: 27px; color: var(--white); }

  .yoga-offer { left: 108px; top: 690px; width: 270px; height: 45px; padding-left: 18px; font-size: 35px; color: var(--red); }
  .yoga-rule { left: 108px; top: 736px; width: 257px; height: 2px; background: var(--amber); }
  .yoga-claim { left: 108px; top: 740px; width: 257px; height: 42px; padding-left: 18px; font-size: 31px; color: var(--teal); }

  .location { left: 99px; top: 842px; width: 554px; text-align: center; font-size: 17px; color: var(--ink); }
</style>
</head>
<body>
<div class="canvas">
  <div class="sheet"></div>

  <div class="abs gym-photo" role="img" aria-label="Photo of people training hard on rowing machines in a gym"></div>
  <svg class="abs red-band" width="422" height="100" viewBox="0 0 422 100" aria-hidden="true">
    <polygon points="0,0 422,0 0,100" fill="var(--red)"/>
  </svg>
  <div class="abs display band-url">IRONPULSEVO.COM</div>

  <div class="abs display gym-name">IronPulse Vo</div>
  <p class="abs body-copy gym-copy">IronPulse Vo is a 25,000 square feet fitness coaching facility We offer group and individual coaching, utilizing the IronPulse methodology. IronPulse workouts are comprised of constantly varied functional movements (like pushing, pulling, squatting, etc.) executed at high intensity in a safe environment.</p>

  <div class="abs tag display gym-offer">$99 INTRO SESSION</div>
  <div class="abs tag display gym-claim">LARGEST IRONPULSE IN TEXAS.</div>

  <div class="abs yoga-mark"></div>
  <div class="abs display yoga-name">ZenLoftVo</div>
  <p class="abs body-copy yoga-copy">So what are you looking for in your yoga practice? Whether it’s pushing the limits of physical fitness, clearing your mind from the chaos of day to day life, or becoming centered through a deeper and more meaningful spiritual exercise, we have the right class, location, and instructor to fit your personal needs.</p>

  <div class="abs yoga-photo" role="img" aria-label="Photo of a yoga class meditating in a bright, warm studio"></div>
  <svg class="abs teal-band" width="413" height="100" viewBox="0 0 413 100" aria-hidden="true">
    <polygon points="0,100 413,0 413,100" fill="var(--teal)"/>
  </svg>
  <div class="abs display band-url-teal">ZENLOFTVO.COM</div>

  <div class="abs tag display yoga-offer">ZENLOFTVO $69/MO</div>
  <div class="abs yoga-rule"></div>
  <div class="abs tag display yoga-claim">UNLIMITED SESSIONS.</div>

  <div class="abs display location">LOCATED NORTH RIVERSIDE HOUSTON (NRVO) ADDRESS: 4817 MARLOW PKWY HOUSTON, TX</div>
</div>
</body>
</html>
```